Create a memorable Stationary for Security Software Company

Velbrantix is the worldwide leader in securing the Internet. Making Internet communications and critical data secure, reliable and available everywhere has been and continues to be our ongoing vision. We are committed to staying focused on real customer needs and to developing new and innovative security solutions that redefine the security landscape.

Industry/Entity Type

Internet

Font styles to use
Serif
Sans Serif
Script

Colors
0792cd
33a6d7
85cae6

```html
<!DOCTYPE html>
<html lang="en">
<head>
<meta charset="utf-8">
<title>Velbrantix Business Card</title>
<link rel="stylesheet" href="https://fonts.googleapis.com/css2?family=Arimo:wght@400;700&family=Questrial&display=swap">
<style>
  :root {
    --brand-deep: #0792cd;
    --brand-mid: #33a6d7;
    --brand-light: #85cae6;
    --card-pale: #bfe4f4;
    --back-dark: #5f8fa6;
    --ink-grey: #5a6870;
    --text-white: #eaf7fd;
    --page-bg: #e9eef1;
  }
  * { margin: 0; padding: 0; box-sizing: border-box; }
  html, body { width: 1200px; height: 950px; overflow: hidden; background: var(--page-bg); }
  .stage { position: relative; width: 1200px; height: 950px; }
  .card { position: absolute; left: 250px; width: 700px; height: 400px; box-shadow: 0 6px 18px rgba(0,0,0,0.18); }
  .card-front { top: 50px; }
  .card-back { top: 500px; }
  .card svg { display: block; }
  .brand-name { font-family: "Questrial", sans-serif; font-size: 38px; fill: var(--brand-deep); }
  .person-name { font-family: "Arimo", sans-serif; font-weight: 700; font-size: 24px; fill: var(--brand-deep); letter-spacing: 1px; }
  .person-role { font-family: "Arimo", sans-serif; font-size: 17px; fill: var(--ink-grey); letter-spacing: 1px; }
  .contact-line { font-family: "Arimo", sans-serif; font-size: 19px; fill: var(--text-white); }
  .back-web { font-family: "Questrial", sans-serif; font-size: 17px; fill: #3e6a80; letter-spacing: 5px; }
  .back-name { font-family: "Questrial", sans-serif; font-size: 40px; fill: #2f7ea4; }
</style>
</head>
<body>
<div class="stage">

  <div class="card card-front">
    <svg width="700" height="400" viewBox="0 0 700 400">
      <defs>
        <linearGradient id="frontSky" x1="0" y1="0" x2="1" y2="1">
          <stop offset="0" stop-color="#a6dbf1"/>
          <stop offset="1" stop-color="var(--brand-light)"/>
        </linearGradient>
        <linearGradient id="frontSea" x1="0" y1="0" x2="0" y2="1">
          <stop offset="0" stop-color="var(--brand-mid)"/>
          <stop offset="1" stop-color="var(--brand-deep)"/>
        </linearGradient>
      </defs>
      <rect class="card-base" width="700" height="400" fill="url(#frontSky)"/>
      <!-- wave bands -->
      <path class="wave-pale" d="M0 170 C160 140 330 150 460 185 C560 210 640 215 700 205 L700 400 L0 400 Z" fill="#d4eef9"/>
      <path class="wave-mid" d="M0 185 C170 160 330 170 460 200 C560 222 640 228 700 220 L700 400 L0 400 Z" fill="var(--brand-mid)"/>
      <path class="wave-light" d="M0 200 C180 178 340 190 470 215 C570 234 640 240 700 235 L700 400 L0 400 Z" fill="var(--brand-light)"/>
      <path class="wave-deep" d="M0 222 C190 200 350 212 480 236 C575 254 645 258 700 254 L700 400 L0 400 Z" fill="url(#frontSea)"/>

      <!-- brand mark -->
      <circle class="brand-dot" cx="95" cy="90" r="26" fill="var(--brand-mid)"/>
      <text class="brand-name" x="132" y="104">Velbrantix</text>

      <!-- person -->
      <text class="person-name" x="655" y="105" text-anchor="end">LENA MARSH</text>
      <text class="person-role" x="655" y="128" text-anchor="end">PRESIDENT</text>

      <!-- contact -->
      <g class="contact-block" text-anchor="end">
        <text class="contact-line" x="640" y="262">2417 Harbor Crest Lane</text>
        <text class="contact-line" x="640" y="286">Brookvale, NY 11902</text>
        <text class="contact-line" x="640" y="316">512 3094 7761</text>
        <text class="contact-line" x="640" y="340">512 3094 7762</text>
        <text class="contact-line" x="640" y="364">lena@velbrantix.com</text>
        <text class="contact-line" x="640" y="388">www.velbrantix.com</text>
      </g>
      <g class="contact-icons" fill="var(--text-white)">
        <path class="icon-phone" d="M650 303 q8 -5 16 0 l-2 4 h-3 l-1 -2 h-4 l-1 2 h-3 z M652 309 h12 v7 h-12 z"/>
        <path class="icon-fax" d="M653 324 h10 v4 h-10 z M650 329 h16 v8 h-16 z"/>
        <path class="icon-mail" d="M650 352 h16 v11 h-16 z" />
        <path d="M650 352 l8 6 l8 -6" fill="none" stroke="#1a86bd" stroke-width="1.5"/>
        <circle class="icon-web" cx="658" cy="382" r="7"/>
      </g>
    </svg>
  </div>

  <div class="card card-back">
    <svg width="700" height="400" viewBox="0 0 700 400">
      <defs>
        <linearGradient id="backSky" x1="0" y1="0" x2="1" y2="1">
          <stop offset="0" stop-color="var(--card-pale)"/>
          <stop offset="0.55" stop-color="#8cc3dc"/>
          <stop offset="1" stop-color="var(--back-dark)"/>
        </linearGradient>
      </defs>
      <rect class="card-base" width="700" height="400" fill="url(#backSky)"/>
      <circle class="brand-dot" cx="246" cy="180" r="30" fill="#3f93bd"/>
      <text class="back-name" x="290" y="195">Velbrantix</text>
      <text class="back-web" x="350" y="262" text-anchor="middle">www.velbrantix.com</text>
    </svg>
  </div>

</div>
</body>
</html>
```